Create a PPTX template for our business

We need a Powerpoint and Keynote template design for a new company called "Quorvell" We connect hotel guests to hotel employees through text messaging so guests can ask for what they need during their stay. The name "Quorvell" is derived from the word "Affinity" which is how we want our hotel customer's employees and their guests to feel about each other. The color palette chosen is meant to evoke feelings of "warmth" and "comfort," which is how most people feel when they have a strong affinity to each other. The "-ium" ending of Quorvell is intended to give a technological feel to our business since we use technology to connect people together.

A *.ai file is included which contains our logo.

```html
<!DOCTYPE html>
<html lang="en">
<head>
<meta charset="utf-8">
<title>Quorvell Presentation Template</title>
<link rel="stylesheet" href="https://fonts.googleapis.com/css2?family=PT+Sans+Narrow:wght@400;700&family=PT+Sans:ital@1&display=swap">
<style>
:root{
  --stage:#1a2326;
  --teal-dark:#17716c;
  --teal:#2a9a92;
  --teal-mid:#4fbdb5;
  --aqua-top:#7fd2cc;
  --aqua-pale:#d8f3f6;
  --aqua-light:#eafafc;
  --lime:#d7dd2c;
  --lime-dark:#b9c21e;
  --cream:#fdfbe1;
  --heading:#1b6a66;
  --text:#1f3b3c;
  --muted:#3f8c89;
  --footer-text:#f3f9e6;
}
*{box-sizing:border-box;margin:0;padding:0}
html,body{width:1200px;height:900px;overflow:hidden;background:var(--stage)}
body{position:relative;font-family:"PT Sans Narrow",Arial Narrow,sans-serif;color:var(--text)}
.slide{position:absolute;width:586px;height:438px;overflow:hidden;
  background:linear-gradient(180deg,var(--aqua-pale) 0%,var(--aqua-light) 100%)}
.slide--1{left:10px;top:8px}
.slide--2{left:605px;top:8px}
.slide--3{left:10px;top:454px}
.slide--4{left:605px;top:454px}

/* cover */
.cover-top{position:absolute;left:0;top:0;width:100%;height:256px;
  background:linear-gradient(180deg,var(--aqua-top) 0%,#a9e3e3 60%,#c8eeee 100%)}
.cover-bottom{position:absolute;left:0;top:260px;width:100%;height:136px;
  background:linear-gradient(180deg,var(--cream),#fbf7cf)}
.cover-rule{position:absolute;left:0;top:255px;width:100%;height:5px;background:var(--lime)}
.portrait-ring{position:absolute;left:20px;top:152px;width:214px;height:214px;border-radius:50%;
  background:var(--lime);padding:5px}
.portrait-ring::before{content:"";position:absolute;inset:5px;border-radius:50%;background:var(--teal-mid)}
.portrait{position:absolute;inset:11px;border-radius:50%;
  background:radial-gradient(circle at 50% 40%,#e8d4c4 0%,#b89a86 30%,#3a3d44 70%,#2a2d33 100%)}
.cover-title{position:absolute;right:34px;top:96px;font-weight:700;font-size:34px;color:var(--heading);letter-spacing:-.2px}
.cover-sub{position:absolute;right:34px;top:140px;width:360px;text-align:right;font-size:13.5px;line-height:19px;color:var(--muted)}
.brand-name{position:absolute;left:330px;top:310px;width:232px;text-align:right;font-size:40px;color:#5d6466;letter-spacing:1px}

/* title flag */
.slide-title{position:absolute;left:0;top:12px;height:30px;display:flex;align-items:center}
.slide-title::before{content:"";width:21px;height:28px;margin-right:7px;background:var(--teal);
  clip-path:polygon(0 0,100% 0,100% 100%,0 100%,0 80%,55% 50%)}
.slide-title h2{font-size:25px;font-weight:700;color:var(--heading)}

.section-head{position:absolute;left:44px;top:72px;font-size:17px;font-weight:700;color:var(--heading)}
.checklist{position:absolute;left:46px;top:100px;list-style:none;font-size:12.5px;line-height:19px}
.checklist li{position:relative;padding-left:20px}
.checklist svg{position:absolute;left:0;top:3px;width:13px;height:13px}
.slide--3 .checklist{width:470px}

.team-photo{position:absolute;left:210px;top:94px;width:346px;height:277px;
  background:linear-gradient(180deg,rgba(234,250,252,0) 0%,#8aa1a8 10%,#4b5660 45%,#7f8d94 70%,rgba(220,236,240,.2) 100%);
  -webkit-mask:linear-gradient(90deg,transparent,#000 8%,#000 92%,transparent);
  mask:linear-gradient(90deg,transparent,#000 8%,#000 92%,transparent)}

/* footer */
.footer{position:absolute;left:0;bottom:0;width:100%;height:42px;
  background:linear-gradient(180deg,var(--teal) 0%,var(--teal-dark) 100%);
  border-top:3px solid var(--lime);display:flex;align-items:center}
.slide-num{position:absolute;left:16px;top:8px;width:30px;height:26px;background:var(--lime-dark);
  border:1px solid #e9ee7a;color:#fff;font-size:16px;display:flex;align-items:center;justify-content:center;font-family:"PT Sans",sans-serif}
.footer-date{position:absolute;left:92px;top:11px;font-size:15px;color:var(--footer-text);font-family:"PT Sans",sans-serif}
.tagline{position:absolute;left:63px;top:11px;font-size:13.5px;font-style:italic;color:var(--footer-text);font-family:"PT Sans",sans-serif}
.btn{position:absolute;top:7px;height:27px;background:linear-gradient(180deg,#e5ea4a,var(--lime-dark));
  color:#3d4a18;font-size:12px;display:flex;align-items:center;justify-content:center;font-family:"PT Sans",sans-serif}
.btn--start{left:524px;width:44px;border-radius:4px}
.btn--back{left:462px;width:48px;clip-path:polygon(10px 0,100% 0,100% 100%,10px 100%,0 50%);padding-left:6px}
.btn--next{left:518px;width:50px;clip-path:polygon(0 0,calc(100% - 10px) 0,100% 50%,calc(100% - 10px) 100%,0 100%);padding-right:6px}
</style>
</head>
<body>

<svg width="0" height="0" style="position:absolute">
  <symbol id="tick" viewBox="0 0 13 13">
    <rect x="0.75" y="2.75" width="9.5" height="9.5" fill="none" stroke="#2b4a4a" stroke-width="1.3"/>
    <path d="M2.8 7 L5.3 9.6 L12 1.5" fill="none" stroke="#2b4a4a" stroke-width="2"/>
  </symbol>
</svg>

<section class="slide slide--1">
  <div class="cover-top"></div>
  <div class="cover-bottom"></div>
  <div class="cover-rule"></div>
  <h1 class="cover-title">Project Title Here</h1>
  <p class="cover-sub">Subtext here Subtext here Subtext here Subtext here Subtext here Subtext here Subtext here Subtext here</p>
  <div class="portrait-ring"><div class="portrait" role="img" aria-label="Portrait photo of the presenter"></div></div>
  <div class="brand-name">Quorvell</div>
  <footer class="footer">
    <span class="slide-num">01</span>
    <span class="footer-date">01/02/15</span>
    <span class="btn btn--start">Start</span>
  </footer>
</section>

<section class="slide slide--2">
  <div class="slide-title"><h2>Slide Title Presentation</h2></div>
  <footer class="footer">
    <span class="slide-num">02</span>
    <span class="tagline">Tagline/Slogan about Your Company</span>
    <span class="btn btn--back">Back</span>
    <span class="btn btn--next">Next</span>
  </footer>
</section>

<section class="slide slide--3">
  <div class="slide-title"><h2>Slide Title Presentation</h2></div>
  <h3 class="section-head">Something About Your Business</h3>
  <ul class="checklist">
    <li><svg><use href="#tick"/></svg>High volume local boutique real estate company</li>
    <li><svg><use href="#tick"/></svg>Specialize in selling homes throughout the San Francisco Bay Area</li>
    <li><svg><use href="#tick"/></svg>Focus on modern marketing techniques and thinking outside the box</li>
    <li><svg><use href="#tick"/></svg>“High Tech and High Touch” approach to real estate</li>
    <li><svg><use href="#tick"/></svg>Certified Green Business Everything is done and stored online. No File Cabinets in our offices!</li>
    <li><svg><use href="#tick"/></svg>Exceptional web presence far beyond other local real estate companies</li>
    <li><svg><use href="#tick"/></svg>Clean, streamline, and hip marketing materials</li>
    <li><svg><use href="#tick"/></svg>A company constantly looking into the latest real estate trends, tools, and technology to better assist their agents and clients sell homes in the modern world, all while embracing tried and true real estate values and practices as well</li>
    <li><svg><use href="#tick"/></svg>Leading authority for architectural homes and recognized world wide</li>
    <li><svg><use href="#tick"/></svg>Not Just Modern Homes! We focus on Modern Real Estate<br>Practices through and through.</li>
  </ul>
  <footer class="footer">
    <span class="slide-num">03</span>
    <span class="tagline">Tagline/Slogan about Your Company</span>
    <span class="btn btn--back">Back</span>
    <span class="btn btn--next">Next</span>
  </footer>
</section>

<section class="slide slide--4">
  <div class="slide-title"><h2>Slide Title Presentation</h2></div>
  <h3 class="section-head">Our Services</h3>
  <ul class="checklist">
    <li><svg><use href="#tick"/></svg>Handymen</li>
    <li><svg><use href="#tick"/></svg>Contractors</li>
    <li><svg><use href="#tick"/></svg>Stagers</li>
    <li><svg><use href="#tick"/></svg>Painters</li>
    <li><svg><use href="#tick"/></svg>Cleaners</li>
    <li><svg><use href="#tick"/></svg>Movers</li>
    <li><svg><use href="#tick"/></svg>Storage companies</li>
    <li><svg><use href="#tick"/></svg>Landscapers</li>
    <li><svg><use href="#tick"/></svg>Estate Sale Professionals</li>
    <li><svg><use href="#tick"/></svg>Lawyers</li>
    <li><svg><use href="#tick"/></svg>Mortgage Brokers</li>
    <li><svg><use href="#tick"/></svg>Inspectors</li>
  </ul>
  <div class="team-photo" role="img" aria-label="Group photo of a business team standing together"></div>
  <footer class="footer">
    <span class="slide-num">04</span>
    <span class="tagline">Tagline/Slogan about Your Company</span>
    <span class="btn btn--back">Back</span>
    <span class="btn btn--next">Next</span>
  </footer>
</section>

</body>
</html>
```